We need a new business card that reflects who we are. Professional, classy, modern, and service ori

We need a business card design for a window coverings design company in Kansas City called Bright Lane Interiors. We offer professional, modern, and high quality window covering products. We are looking to portray an image of a big, national franchise. We are a 5 location (with showrooms) business with 10 professional designers and 4 professional installers. These cards will be used with Thank you cards, given to realtors, and asked for referrals with.

Target Market(s)

Kansas City

Industry/Entity Type

Business

Contact Information for Business Card

We would like our card to look clean and simple on the front, featuring our logo and Marlow Fenwick's. Our designers' phone numbers and emails should be displayed as well as their title.

Font styles to use
Sans Serif

Colors

Designer to choose colors to be used in the design.

Requirements
Must have
• Front - Logos, name, phone number, email address
• Back - Showroom locations, social media? Appt date/time?
Nice to have
• I would like a clean and modern look (not contemporary. I like a white background, but I am open to ideas. Looking for a "National chain" look for a small business.
Should not have
• Too much busyness.

```html
<!DOCTYPE html>
<html lang="en">
<head>
<meta charset="utf-8">
<title>Bright Lane Interiors – Business Card</title>
<link href="https://fonts.googleapis.com/css2?family=Roboto:wght@400;500&family=Roboto+Condensed:wght@500&family=Libre+Baskerville&display=swap" rel="stylesheet">
<style>
  :root {
    --bg: #e6e6e6;
    --paper: #f3f3f3;
    --red: #c84248;
    --grey: #8c9094;
    --ink: #111111;
    --text: #4a4a4a;
    --dots: #8a8a8a;
    --white: #ffffff;
  }
  * { margin: 0; padding: 0; box-sizing: border-box; }
  html, body { width: 1200px; height: 960px; overflow: hidden; }
  body { background: var(--bg); font-family: "Roboto", Arial, sans-serif; position: relative; }

  .card {
    position: absolute; width: 600px; height: 343px;
    background: var(--paper);
    box-shadow: 0 2px 6px rgba(0,0,0,0.18);
  }
  .card--front { left: 314px; top: 113px; }
  .card--back  { left: 311px; top: 472px; }

  /* Front */
  .stripe-panel { position: absolute; left: 0; top: 10px; width: 193px; height: 322px; display: flex; }
  .stripe-panel .band--grey { background: var(--grey); width: 53px; }
  .stripe-panel .band--red  { background: var(--red); width: 93px; }
  .stripe-panel .band--grey:last-child { width: 47px; }
  .brand-name {
    position: absolute; left: 0; top: 70px; width: 193px; text-align: center;
    font-family: "Roboto", Arial, sans-serif; font-weight: 500; font-size: 26px;
    letter-spacing: 0.5px; color: var(--white);
  }

  .identity { position: absolute; right: 46px; top: 186px; text-align: right; }
  .identity__name { font-family: "Roboto Condensed", Arial, sans-serif; font-weight: 500; font-size: 24px; color: var(--red); line-height: 1; }
  .identity__title { font-family: "Roboto Condensed", Arial, sans-serif; font-weight: 500; font-size: 16px; color: var(--ink); margin-top: 3px; letter-spacing: 0.3px; }

  .contact { position: absolute; right: 46px; top: 248px; list-style: none; }
  .contact li { display: flex; align-items: center; justify-content: flex-end; gap: 9px; font-size: 14px; color: var(--text); height: 19.5px; }
  .contact svg { width: 12px; height: 12px; fill: var(--red); }

  /* Back */
  .brand-lockup { position: absolute; left: 40px; top: 128px; width: 246px; text-align: center; }
  .brand-lockup__name {
    display: inline-flex; align-items: center; gap: 8px;
    font-family: "Roboto", Arial, sans-serif; font-weight: 400; font-size: 22px; color: var(--ink); white-space: nowrap;
  }
  .brand-lockup__square { width: 14px; height: 14px; background: var(--red); }
  .brand-lockup__tagline { font-family: "Libre Baskerville", Georgia, serif; font-size: 10.5px; color: var(--ink); margin-top: 4px; white-space: nowrap; }

  .showrooms { position: absolute; right: 53px; top: 43px; text-align: right; }
  .showrooms__heading { font-weight: 500; font-size: 14px; color: var(--red); letter-spacing: 0.2px; line-height: 18px; }
  .showrooms__list { list-style: none; }
  .showrooms__list li { font-weight: 500; font-size: 14.5px; color: var(--text); line-height: 18px; letter-spacing: 0.3px; }

  .partner { position: absolute; right: 53px; top: 157px; display: flex; align-items: center; gap: 5px; }
  .partner__name { font-weight: 500; font-size: 12px; color: #5d6870; }
  .partner__badge { width: 16px; height: 16px; border-radius: 50%; background: #f08a24; }

  .social { position: absolute; right: 53px; top: 185px; display: flex; gap: 2px; }
  .social span { width: 18px; height: 18px; border-radius: 50%; background: var(--red); }

  .appointment { position: absolute; left: 52px; right: 50px; color: var(--red); font-size: 16px; display: flex; align-items: baseline; }
  .appointment--name { top: 237px; }
  .appointment--when { top: 278px; }
  .appointment .fill { flex: 1; border-bottom: 1.5px dotted var(--dots); margin: 0 2px 0 8px; height: 1px; transform: translateY(-3px); }
  .appointment .label-gap { margin-left: 2px; }
  .appointment .ampm { font-size: 12px; margin-left: 6px; }
</style>
</head>
<body>

<section class="card card--front" aria-label="Business card front">
  <div class="stripe-panel">
    <div class="band--grey"></div>
    <div class="band--red"></div>
    <div class="band--grey"></div>
  </div>
  <p class="brand-name">Bright Lane</p>

  <div class="identity">
    <p class="identity__name">JANE MILLER</p>
    <p class="identity__title">DESIGNER</p>
  </div>

  <ul class="contact">
    <li>913.555.0148
      <svg viewBox="0 0 24 24" aria-hidden="true"><path d="M6.6 10.8a15.2 15.2 0 0 0 6.6 6.6l2.2-2.2a1 1 0 0 1 1-.25 11.4 11.4 0 0 0 3.6.57 1 1 0 0 1 1 1V20a1 1 0 0 1-1 1A17 17 0 0 1 3 4a1 1 0 0 1 1-1h3.5a1 1 0 0 1 1 1c0 1.25.2 2.45.57 3.57a1 1 0 0 1-.25 1z"/></svg>
    </li>
    <li>info@brightlaneinteriors.com
      <svg viewBox="0 0 24 24" aria-hidden="true"><path d="M2 5h20v2l-10 6L2 7z"/><path d="M2 9l10 6 10-6v10H2z"/></svg>
    </li>
    <li>brightlaneinteriors.com
      <svg viewBox="0 0 24 24" aria-hidden="true"><circle cx="12" cy="12" r="10"/></svg>
    </li>
  </ul>
</section>

<section class="card card--back" aria-label="Business card back">
  <div class="brand-lockup">
    <p class="brand-lockup__name"><span class="brand-lockup__square"></span>Bright Lane Interiors</p>
    <p class="brand-lockup__tagline">Blinds, Shades, Shutters, Draperies &amp; Decor</p>
  </div>

  <div class="showrooms">
    <p class="showrooms__heading">SHOWROOM LOCATIONS</p>
    <ul class="showrooms__list">
      <li>RIVERSIDE</li>
      <li>MAPLE HEIGHTS</li>
      <li>CEDAR POINT</li>
      <li>NORTH HILLS</li>
      <li>EAST BEND</li>
    </ul>
  </div>

  <div class="partner">
    <span class="partner__name">Marlow Fenwick</span>
    <span class="partner__badge"></span>
  </div>

  <div class="social" aria-label="Social media">
    <span></span><span></span><span></span><span></span>
  </div>

  <div class="appointment appointment--name">
    <span>Name :</span><span class="fill"></span>
  </div>
  <div class="appointment appointment--when">
    <span>Date :</span><span class="fill"></span>
    <span class="label-gap">Time :</span><span class="fill"></span>
    <span class="ampm">AM/PM</span>
  </div>
</section>

</body>
</html>
```